Creative, fresh business card design for Ripplecraft Facades

We need a fresh, creative business card design for Ripplecraft Facades. We are the manufacturer of Ripplecraft Facades in Australia. Wall panels are 2400 x 1200mm panels made from MDF and feature 3D patterns on the face of the panel. The colours to be used are green, silver/grey and white RGB
Red 187
Green 207
Blue 65.

An idea is to possibly use a watermark of one of our designs as a background (like on the "Grids" design on the left hand side of page 2 of our brochure).

Target Market(s)

Interior designers, architects, builders and home renovators

Industry/Entity Type

Business

Contact Information for Business Card

Details to go on the card are:
Our logo (attached),
Slogan: "Decorative panels for interiors and exteriors",
Contact name,
Position,
Mobile phone number,
Business address,
Business phone,
Business fax,
Website and
Email address.

I have attached a few images of our panels and our brochure for reference.

The colours of the business card should feature our logo colours which are: RGB
Red 187
Green 207
Blue 65

Requirements
Must have
• Very modern fonts and design. Some of the designs shown especially the "Prisms" design which is a popular design.
Nice to have
• Creative but simple design. Very contemporary.
Should not have
• Anything ornate or old fashioned.

```html
<!DOCTYPE html>
<html lang="en">
<head>
<meta charset="utf-8">
<title>Ripplecraft Facades – Business Card</title>
<link rel="stylesheet" href="https://fonts.googleapis.com/css2?family=Arimo:wght@400;700&display=swap">
<style>
  :root {
    --page: #d9d6d2;
    --card: #eceeed;
    --card-edge: #f7f8f8;
    --green: #9dc12f;
    --green-light: #c2d97a;
    --slate: #5c5f66;
    --ink: #1d1e20;
    --muted: #6f7276;
    --white: #ffffff;
  }
  * { margin: 0; padding: 0; box-sizing: border-box; }
  html, body {
    width: 1200px; height: 969px; overflow: hidden;
    background: var(--page);
    font-family: "Arimo", Arial, sans-serif;
  }
  .card {
    position: absolute; left: 100px; top: 200px;
    width: 1000px; height: 569px;
    background: linear-gradient(160deg, var(--card-edge), var(--card));
    border: 1px solid #ffffff;
    box-shadow: 0 10px 30px rgba(0,0,0,0.12);
    overflow: hidden;
  }
  .green-band {
    position: absolute; top: 43px; left: 0; right: 0; height: 134px;
    background: var(--green);
  }
  .brand-block {
    position: absolute; top: 43px; left: 603px; width: 319px; height: 184px;
    background: var(--green-light);
    border-left: 3px solid var(--white);
    border-right: 3px solid var(--white);
  }
  .brand-square {
    position: absolute; left: 130px; top: 38px;
    width: 58px; height: 58px; background: var(--white);
  }
  .slate-bar {
    position: absolute; top: 184px; left: 0; right: 0; height: 43px;
    background: var(--slate);
  }
  .brand-name {
    position: absolute; top: 184px; left: 603px; width: 319px; height: 43px;
    line-height: 43px; text-align: center;
    color: var(--white); font-size: 23px; font-weight: 400;
  }
  .person { position: absolute; left: 47px; top: 72px; }
  .person-name {
    color: var(--white); font-size: 31px; font-weight: 700; letter-spacing: 0.5px;
  }
  .person-role {
    color: var(--white); font-size: 26px; font-weight: 400; margin-top: 6px;
  }
  .slogan {
    position: absolute; top: 232px; left: 603px; width: 319px;
    text-align: center; color: var(--muted);
    font-size: 18px; letter-spacing: 2.6px; line-height: 25px;
  }
  .contacts { position: absolute; left: 47px; top: 364px; list-style: none; }
  .contacts li {
    display: flex; align-items: center; height: 38.5px;
    color: var(--slate); font-size: 24px;
  }
  .contacts svg { width: 24px; height: 24px; margin-right: 18px; fill: var(--green); }
  .address {
    position: absolute; right: 73px; top: 442px;
    text-align: right; color: var(--ink); font-size: 24px; line-height: 33px;
  }
</style>
</head>
<body>
  <div class="card">
    <div class="green-band"></div>
    <div class="slate-bar"></div>
    <div class="brand-block"><div class="brand-square"></div></div>
    <div class="brand-name">Ripplecraft Facades</div>

    <div class="person">
      <div class="person-name">MARCUS HALE</div>
      <div class="person-role">CEO&amp;Founder</div>
    </div>

    <p class="slogan">decorative panels for<br>interiors &amp; exteriors</p>

    <ul class="contacts">
      <li>
        <svg viewBox="0 0 24 24" aria-hidden="true"><path d="M6.6 10.8a15.1 15.1 0 0 0 6.6 6.6l2.2-2.2a1 1 0 0 1 1-.25 11.4 11.4 0 0 0 3.6.57 1 1 0 0 1 1 1V20a1 1 0 0 1-1 1A17 17 0 0 1 3 4a1 1 0 0 1 1-1h3.5a1 1 0 0 1 1 1c0 1.25.2 2.45.57 3.57a1 1 0 0 1-.25 1z"/></svg>
        (555) 210-4471
      </li>
      <li>
        <svg viewBox="0 0 24 24" aria-hidden="true"><path d="M7 3h10v5H7z M3 9h18v8h-3v-3H6v3H3z M7 15h10v6H7z"/></svg>
        (555) 210-4472
      </li>
      <li>
        <svg viewBox="0 0 24 24" aria-hidden="true"><path d="M2 5h20v14H2z" /><path d="M2 5l10 8 10-8" fill="none" stroke="#eceeed" stroke-width="2"/></svg>
        mhale@ripplecraftfacades.com
      </li>
      <li>
        <svg viewBox="0 0 24 24" aria-hidden="true"><circle cx="12" cy="12" r="10"/><path d="M2 12h20M12 2c3 3 3 17 0 20M12 2c-3 3-3 17 0 20" fill="none" stroke="#eceeed" stroke-width="1.5"/></svg>
        www.ripplecraftfacades.com
      </li>
    </ul>

    <address class="address" style="font-style:normal">
      42 Tidewater Road<br>
      Geelong, Victoria 3220
    </address>
  </div>
</body>
</html>
```